New business card for a regional office of a US M&A company

We need business card for a finance company, office based in Hong Kong , our Head office is in US, our business is to Merge and acquires companies , the new office will be a regional office for the Asia Pacific region. We want to use the head office logo as attached ( but don't have to be exactly the same, can be a variation to it) as a base and then add Asia Pacific alongside the logo.
We would prefer to have be bilingual Eng + Chinese, although we don't really have Chinese company name .

Industry/Entity Type

Business

Contact Information for Business Card

Clara Jo Tsang
 

VP,
APAC M&A Operations
Orin Vantage Asia Pacific Limited
 
Unit 1407, K18
18 Tai Lok Shan Road, 
Hong Kong 
 
M: +852 6038 1742
T : +852 2836 4100
F : +852 2836 4177
VOIP: 4158
 
cjtsang@orinvantage.com

Font styles to use
Serif
Sans Serif

Colors

Designer to choose colors to be used in the design.

Requirements
Must have
• APAC Office

```html
<!DOCTYPE html>
<html lang="en">
<head>
<meta charset="utf-8">
<title>Orin Vantage – Business Card</title>
<link href="https://fonts.googleapis.com/css2?family=Roboto:wght@400;700&family=Roboto+Condensed:wght@500&display=swap" rel="stylesheet">
<style>
  :root {
    --navy: #0e2943;
    --sky: #1eadd1;
    --paper: #eef0f2;
    --ink: #4a4f55;
    --backdrop: #e7e4df;
  }
  * { margin: 0; padding: 0; box-sizing: border-box; }
  html, body { width: 1200px; height: 960px; overflow: hidden; }
  body { background: var(--backdrop); position: relative; font-family: "Roboto", sans-serif; }

  .card { position: absolute; overflow: hidden; box-shadow: 0 2px 4px rgba(0,0,0,.35); }

  /* Front */
  .card-front { left: 314px; top: 113px; width: 601px; height: 343px; background: var(--paper); }
  .front-shape { position: absolute; inset: 0; }
  .front-brand {
    position: absolute; left: 0; width: 315px; top: 0; height: 343px;
    display: flex; flex-direction: column; align-items: center; justify-content: center; gap: 22px;
    padding-top: 40px;
  }
  .brand-square { width: 42px; height: 42px; background: #fff; }
  .front-brand .brand-name { color: var(--sky); font-weight: 700; font-size: 32px; letter-spacing: .5px; }

  .details { position: absolute; right: 30px; top: 0; text-align: right; color: var(--ink); }
  .person-name { position: absolute; right: 0; top: 38px; white-space: nowrap;
    font-family: "Roboto Condensed", sans-serif; font-weight: 500; font-size: 21px; color: var(--navy); }
  .person-title { position: absolute; right: 0; top: 64px; font-size: 14px; color: var(--sky); }
  .address { position: absolute; right: 0; top: 126px; font-size: 14px; line-height: 19px; white-space: nowrap; }
  .phones { position: absolute; right: 0; top: 228px; list-style: none; font-size: 14px; line-height: 19.5px; white-space: nowrap; }
  .phones li { display: flex; align-items: center; justify-content: flex-end; gap: 6px; }
  .phones svg { width: 12px; height: 13px; fill: var(--navy); }
  .voip { position: absolute; right: 0; top: 295px; font-size: 14px; white-space: nowrap; }

  /* Back */
  .card-back { left: 311px; top: 472px; width: 600px; height: 343px; background: var(--sky);
    display: flex; flex-direction: column; align-items: center; }
  .back-square { margin-top: 88px; width: 64px; height: 64px; background: var(--navy); }
  .card-back .brand-name { margin-top: 40px; color: var(--navy); font-weight: 700; font-size: 46px; letter-spacing: .5px; }
  .website { margin-top: 34px; color: var(--navy); font-size: 14px; letter-spacing: 6px; }
</style>
</head>
<body>

<section class="card card-front">
  <svg class="front-shape" viewBox="0 0 601 343" width="601" height="343" aria-hidden="true">
    <polygon points="0,0 187,0 366,170 187,343 0,343" fill="var(--navy)"/>
    <polygon points="187,0 198,0 366,170 198,343 187,343 355,170" fill="var(--navy)"/>
    <polygon points="190,0 201,0 369,170 201,343 190,343 358,170" fill="var(--sky)"/>
  </svg>
  <div class="front-brand">
    <div class="brand-square"></div>
    <div class="brand-name">ORIN VANTAGE</div>
  </div>
  <div class="details">
    <h1 class="person-name">CLARA JO TSANG</h1>
    <p class="person-title">VP</p>
    <p class="address">Unit 1407, K18<br>18 Tai Lok Shan Road<br>Hong Kong<br>APAC M&amp;A Operations<br>Orin Vantage Asia Pacific Limited</p>
    <ul class="phones">
      <li>+852 2836 4100
        <svg viewBox="0 0 24 24"><path d="M6.6 10.8a15.1 15.1 0 0 0 6.6 6.6l2.2-2.2c.3-.3.7-.4 1-.2 1.1.4 2.3.6 3.6.6.6 0 1 .4 1 1V20c0 .6-.4 1-1 1A17 17 0 0 1 3 4c0-.6.4-1 1-1h3.5c.6 0 1 .4 1 1 0 1.3.2 2.5.6 3.6.1.3 0 .7-.2 1z"/></svg>
      </li>
      <li>+852 6038 1742
        <svg viewBox="0 0 24 24"><path d="M7 1h10a2 2 0 0 1 2 2v18a2 2 0 0 1-2 2H7a2 2 0 0 1-2-2V3a2 2 0 0 1 2-2zm0 3v14h10V4zm5 15.5a1 1 0 1 0 0 2 1 1 0 0 0 0-2z"/></svg>
      </li>
      <li>+852 2836 4177
        <svg viewBox="0 0 24 24"><path d="M6 2h10l2 2v5h2a2 2 0 0 1 2 2v9a2 2 0 0 1-2 2H4a2 2 0 0 1-2-2v-9a2 2 0 0 1 2-2h2zm2 2v5h8V5h-1V4zm-2 10v2h12v-2z"/></svg>
      </li>
    </ul>
    <p class="voip">VOIP: 4158</p>
  </div>
</section>

<section class="card card-back">
  <div class="back-square"></div>
  <div class="brand-name">ORIN VANTAGE</div>
  <p class="website">www.orinvantage.com</p>
</section>

</body>
</html>
```